Venture Capital Investment Firm

We are looking to overhaul our existing website (substantially), with only using the same logos (which we can provide).
We are an investment firm that focuses on making loans to late stage technology companies. Our site should ultimately look like other venture capital firms, and look modern and fresh. We have an existing website www.norvellhub.com which this will be replacing, although we will be using a lot of the existing written content, and potentially the numbers of pages we will need, we are not wed to anything else. Please feel free to shoot any questions at any time and thank you in advance for your help!
Websites we like as examples:
https://www.tesmarkfund.com/
https://www.brindlewoodpartners.com/
Target Market(s)
Potential investors who will invest in our firm, as well as potentially companies that are looking to borrow money from us.
Coding
Coded - Design and coding required
Number of Pages Required
5+ page
Colors
Designer to choose colors to be used in the design.
Look and feel

```html
<!DOCTYPE html>
<html lang="en">
<head>
<meta charset="utf-8">
<title>Norvell Hub Partners</title>
<link rel="stylesheet" href="https://fonts.googleapis.com/css2?family=Cinzel:wght@500;700&family=Oswald:wght@400;500&family=Poppins:wght@400;500;600&display=swap">
<style>
:root{
  --navy:#0e0c4c;
  --navy-deep:#0a0940;
  --ink:#15134f;
  --text:#6e6e7a;
  --dark:#222;
  --grey-bg:#efefef;
  --white:#fff;
  --line:#d9d9e2;
}
*{box-sizing:border-box;margin:0;padding:0}
html,body{width:1200px;height:4250px;overflow:hidden;background:var(--white)}
body{font-family:'Poppins',sans-serif;color:var(--text);position:relative}
.abs{position:absolute}

/* header */
.site-header{position:absolute;left:0;top:0;width:1200px;height:83px;background:var(--white)}
.brand{position:absolute;display:flex;align-items:center;gap:12px;font-family:'Cinzel',serif;font-weight:500;color:var(--ink)}
.brand .dot{border-radius:50%;background:var(--ink)}
.site-header .brand{left:78px;top:22px;font-size:26px}
.site-header .brand .dot{width:34px;height:34px}
.main-nav{position:absolute;right:80px;top:22px;display:flex;align-items:center;gap:26px;font-size:14px;color:#444;letter-spacing:.3px}
.main-nav .active{background:var(--navy);color:var(--white);font-weight:600;padding:11px 21px;border-radius:4px}

/* hero */
.hero{position:absolute;left:0;top:83px;width:1200px;height:594px;overflow:hidden;
  background:
    radial-gradient(ellipse 170px 230px at 1040px 260px,rgba(30,40,70,.85),rgba(30,40,70,0) 100%),
    radial-gradient(ellipse 150px 200px at 820px 320px,rgba(40,55,90,.75),rgba(40,55,90,0) 100%),
    radial-gradient(ellipse 90px 90px at 1010px 110px,rgba(214,178,150,.9),rgba(214,178,150,0) 100%),
    radial-gradient(ellipse 80px 80px at 830px 190px,rgba(220,185,160,.85),rgba(220,185,160,0) 100%),
    radial-gradient(ellipse 180px 70px at 930px 500px,rgba(230,234,240,.9),rgba(230,234,240,0) 100%),
    radial-gradient(ellipse 160px 90px at 250px 500px,rgba(200,200,200,.7),rgba(200,200,200,0) 100%),
    linear-gradient(100deg,#f3f6f8 0%,#e6ecf1 45%,#b9c4d1 65%,#6d7a90 82%,#3d4860 100%)}
.hero-title{position:absolute;left:79px;top:140px;font-family:'Oswald',sans-serif;font-weight:500;font-size:40px;line-height:47px;color:var(--navy-deep);text-transform:uppercase}
.hero-sub{position:absolute;left:79px;top:292px;font-family:'Oswald',sans-serif;font-size:26px;color:var(--navy-deep);text-transform:uppercase}
.btn{position:absolute;display:flex;align-items:center;justify-content:center;font-family:'Cinzel',serif;font-weight:700;font-size:18px;border-radius:5px;letter-spacing:.5px}
.btn-solid{background:var(--navy);color:var(--white)}
.btn-light{background:var(--white);color:var(--navy);box-shadow:0 2px 6px rgba(0,0,0,.12)}
.slider-arrow{position:absolute;top:270px;width:46px;height:46px;border-radius:50%;background:rgba(255,255,255,.45);display:flex;align-items:center;justify-content:center}

/* call bar */
.call-bar{position:absolute;left:0;top:677px;width:1200px;height:94px;background:var(--navy)}
.call-bar p{position:absolute;left:79px;top:34px;font-size:19px;color:var(--white)}
.phone-box{position:absolute;left:924px;top:20px;width:198px;height:52px;border:1px solid rgba(255,255,255,.5);border-radius:5px;display:flex;align-items:center;justify-content:center;gap:10px;color:var(--white);font-family:'Cinzel',serif;font-weight:700;font-size:20px}

/* section heads */
.sec-title{position:absolute;left:0;width:1200px;text-align:center;font-family:'Cinzel',serif;font-weight:700;font-size:40px;color:var(--navy)}
.sec-title span{border-left:2px solid var(--navy);padding-left:10px}
.sec-sub{position:absolute;left:0;width:1200px;text-align:center;font-size:16px;color:#333}

/* strategy */
.photo-circle{position:absolute;border-radius:50%}
.strat-circle{width:188px;height:188px;border:4px solid var(--navy);box-shadow:inset 0 0 0 3px #fff}
.strat-name{position:absolute;font-family:'Cinzel',serif;font-weight:700;font-size:20px;color:var(--navy)}
.strat-text{position:absolute;width:330px;font-size:14.5px;line-height:27px;color:var(--text)}
.read-more{position:absolute;font-size:15px;color:var(--navy)}

/* idea */
.idea{position:absolute;left:0;top:1406px;width:1200px;height:645px;background:var(--grey-bg)}
.idea-title{position:absolute;left:139px;top:72px;font-family:'Cinzel',serif;font-weight:700;font-size:40px;line-height:47px;color:var(--navy)}
.idea-bar{position:absolute;left:121px;top:80px;width:2px;height:80px;background:var(--navy)}
.idea-lead{position:absolute;left:139px;top:176px;width:390px;font-weight:600;font-size:15px;line-height:23px;color:var(--dark)}
.idea-text{position:absolute;left:139px;width:410px;font-size:14.5px;line-height:27px;color:var(--text)}
.idea-photo{position:absolute;left:673px;top:92px;width:403px;height:403px;border-radius:50%;
  background:
    radial-gradient(ellipse 60px 70px at 150px 170px,rgba(180,130,100,.7),rgba(180,130,100,0) 100%),
    radial-gradient(ellipse 60px 70px at 260px 160px,rgba(225,200,180,.8),rgba(225,200,180,0) 100%),
    radial-gradient(circle at 50% 50%,#d9d6df 0%,#a9a7c0 45%,#3a3878 72%,#1a1760 100%)}

/* team */
.team-circle{width:260px;height:260px}
.team-mono{background:
  radial-gradient(ellipse 55px 70px at 50% 38%,#bdbdbd,rgba(189,189,189,0) 100%),
  radial-gradient(ellipse 120px 80px at 50% 100%,#1c1c1c,rgba(28,28,28,0) 100%),
  radial-gradient(circle at 50% 45%,#5a5a5a,#121212 80%)}
.team-navy{background:
  radial-gradient(ellipse 55px 70px at 50% 38%,#4a4880,rgba(74,72,128,0) 100%),
  radial-gradient(circle at 50% 45%,#2c2a68,#100e4a 80%)}
.dashed{position:absolute;left:469px;top:2329px;width:260px;height:260px;border-radius:50%;border:2px dotted #777}
.member-name{position:absolute;width:360px;text-align:center;font-family:'Cinzel',serif;font-weight:700;font-size:18px;color:var(--navy)}
.member-role{position:absolute;width:360px;text-align:center;font-size:15px;color:var(--text)}
.contact-dot{position:absolute;width:38px;height:38px;border-radius:50%;background:var(--white);display:flex;align-items:center;justify-content:center}

/* investor */
.investor{position:absolute;left:0;top:2657px;width:1200px;height:280px;
  background:
    linear-gradient(115deg,rgba(255,255,255,0) 60%,rgba(255,255,255,.04) 60%,rgba(255,255,255,.04) 75%,rgba(255,255,255,0) 75%),
    linear-gradient(65deg,rgba(255,255,255,0) 15%,rgba(255,255,255,.03) 15%,rgba(255,255,255,.03) 30%,rgba(255,255,255,0) 30%),
    linear-gradient(120deg,#0b0a45,#141262 55%,#0b0a45)}
.investor .sec-title{color:var(--white)}
.investor .sec-title span{border-color:var(--white)}
.investor .sec-sub{color:#aab}
.field{position:absolute;top:166px;height:51px;background:var(--white);border-radius:4px;font-size:14px;color:#999;padding:17px 22px}
.submit{position:absolute;left:861px;top:166px;width:124px;height:51px;border:2px solid var(--white);border-radius:5px;color:var(--white);font-family:'Cinzel',serif;font-weight:700;font-size:18px;display:flex;align-items:center;justify-content:center}

/* news */
.timeline{position:absolute;left:282px;top:2937px;width:4px;height:985px;background:var(--navy)}
.news-thumb{position:absolute;width:156px;height:156px;border-radius:50%;background:var(--white);box-shadow:0 4px 14px rgba(0,0,0,.14);display:flex;align-items:center;justify-content:center}
.news-thumb div{width:140px;height:140px;border-radius:50%}
.news-date{position:absolute;left:414px;font-weight:600;font-size:15px;color:var(--dark)}
.news-title{position:absolute;left:414px;width:580px;font-family:'Cinzel',serif;font-weight:700;font-size:18.5px;line-height:25px;color:var(--dark)}
.news-text{position:absolute;left:414px;width:420px;font-size:14.5px;line-height:27px;color:var(--text)}

/* footer */
.site-footer{position:absolute;left:0;top:3922px;width:1200px;height:328px;background:var(--navy-deep);color:#c8c8dd;text-align:center}
.site-footer .brand{left:0;width:1200px;justify-content:center;top:48px;font-size:28px;color:var(--white)}
.site-footer .brand .dot{width:34px;height:34px;background:var(--white)}
.foot-line{position:absolute;left:0;width:1200px;font-size:14.5px}
</style>
</head>
<body>

<header class="site-header">
  <div class="brand"><span class="dot"></span>Norvell Hub</div>
  <nav class="main-nav">
    <span class="active">HOME</span><span>STRATEGY</span><span>ABOUT US</span><span>TEAM</span><span>NEWS</span><span>CONTACT</span><span>INVESTORS</span>
  </nav>
</header>

<section class="hero" role="img" aria-label="Photo of two businessmen reviewing a tablet in a bright office">
  <span class="slider-arrow" style="left:14px"><svg width="12" height="18" viewBox="0 0 12 18"><path d="M9 2L3 9l6 7" stroke="#fff" stroke-width="1.6" fill="none"/></svg></span>
  <span class="slider-arrow" style="right:14px"><svg width="12" height="18" viewBox="0 0 12 18"><path d="M3 2l6 7-6 7" stroke="#fff" stroke-width="1.6" fill="none"/></svg></span>
  <h1 class="hero-title">We are a global structured<br>credit investment firm<br>focused on the</h1>
  <p class="hero-sub">Healthcare and technology industries</p>
  <a class="btn btn-solid" style="left:78px;top:352px;width:165px;height:52px">LEARN MORE</a>
  <a class="btn btn-light" style="left:252px;top:352px;width:168px;height:52px">CONTACT US</a>
</section>

<div class="call-bar">
  <p>If you need An have any Question For Contact Us Today !</p>
  <div class="phone-box">
    <svg width="24" height="24" viewBox="0 0 24 24"><circle cx="12" cy="12" r="11" fill="none" stroke="#fff" stroke-width="1.5"/><path d="M8 7c1-1 2 0 2.5 1.2s-.6 1.6-.3 2.4 1.6 2.4 2.6 2.8 1.3-.7 2.2-.4 2 1.4 1.2 2.3c-1.5 1.6-4 .8-6-1.3S6.5 8.5 8 7z" fill="#fff"/></svg>
    555 014 2290
  </div>
</div>

<!-- strategy -->
<h2 class="sec-title" style="top:826px"><span>STRATEGY</span></h2>
<p class="sec-sub" style="top:881px">Partners For Growth Innovative Companies &amp; Their Investors</p>
<div class="photo-circle strat-circle" style="left:401px;top:941px;background:radial-gradient(ellipse 40px 55px at 60% 45%,#7fb3d9,rgba(127,179,217,0) 100%),radial-gradient(ellipse 45px 40px at 65% 85%,#d7b39b,rgba(215,179,155,0) 100%),linear-gradient(135deg,#eef1f4,#c5ced8 60%,#8e9aab)" role="img" aria-label="Hand holding a smartphone showing a health app"></div>
<div class="photo-circle strat-circle" style="left:610px;top:941px;background:radial-gradient(circle at 50% 50%,#e07b5a 0,rgba(224,123,90,0) 22%),radial-gradient(circle at 50% 50%,#4f7a96,#1b3552 60%,#0d1c30)" role="img" aria-label="Hand touching a digital security interface"></div>
<div class="strat-name" style="left:424px;top:1158px">LIFE SCIENCES</div>
<div class="strat-name" style="left:617px;top:1158px">TECHNOLOGY</div>
<p class="strat-text" style="left:251px;top:1193px;text-align:right">We have a long track record of partnering with companies and investors that create and commercialize life science products, with extensive experience</p>
<p class="strat-text" style="left:617px;top:1193px">We uniquely offer sizeable and flexible structured credit financing solutions to innovative technology companies, with a focus on enterprise software</p>
<a class="read-more" style="left:473px;top:1314px">Read More &#9656;</a>
<a class="read-more" style="left:619px;top:1314px">Read More &#9656;</a>

<!-- idea -->
<section class="idea">
  <span class="idea-bar"></span>
  <h2 class="idea-title">NORVELL HUB STARTED<br>WITH A BIG IDEA</h2>
  <p class="idea-lead">Finance Proven Innovation With A Different Approach</p>
  <p class="idea-text" style="top:250px">Norvell Hub is a private investment firm unique in its dual focus on life science and technology credit opportunities. Our ambidextrous approach to investing reflects a broad recognition and appreciation for the critical role intellectual property plays in the successful commercialization of products.</p>
  <p class="idea-text" style="top:424px">We apply our extensive industry expertise to assess the revenue visibility created by these assets and offer a range of creative financing solutions.</p>
  <a class="btn btn-solid" style="left:139px;top:521px;width:167px;height:51px">LEARN MORE</a>
  <div class="idea-photo" role="img" aria-label="Photo of two smiling women colleagues"></div>
</section>

<!-- team -->
<h2 class="sec-title" style="top:2107px"><span>OUR TEAM</span></h2>
<p class="sec-sub" style="top:2161px">Partners For Growth Innovative Companies &amp; Their Investors</p>
<div class="photo-circle team-circle team-mono" style="left:113px;top:2210px" role="img" aria-label="Black and white portrait of a partner in a suit"></div>
<span class="dashed"></span>
<div class="photo-circle team-circle team-navy" style="left:469px;top:2210px" role="img" aria-label="Portrait of a managing partner with navy overlay"></div>
<div class="photo-circle team-circle team-mono" style="left:825px;top:2210px" role="img" aria-label="Black and white portrait of a partner smiling"></div>
<div class="contact-dot" style="left:557px;top:2313px"><svg width="16" height="12" viewBox="0 0 16 12"><rect width="16" height="12" rx="1.5" fill="#0e0c4c"/><path d="M1 1l7 5 7-5" stroke="#fff" stroke-width="1.4" fill="none"/></svg></div>
<div class="contact-dot" style="left:605px;top:2313px"><svg width="12" height="12" viewBox="0 0 12 12"><circle cx="6" cy="6" r="5" fill="#0e0c4c"/></svg></div>
<div class="member-name" style="left:63px;top:2494px">MARCUS ELLERY</div>
<div class="member-role" style="left:63px;top:2522px">Managing Partner</div>
<div class="member-name" style="left:419px;top:2494px">SAMIR OKONJO</div>
<div class="member-role" style="left:419px;top:2522px">Managing Partner</div>
<div class="member-name" style="left:775px;top:2494px">OWEN PARTRIDGE</div>
<div class="member-role" style="left:775px;top:2522px">Partner</div>

<!-- investor -->
<section class="investor">
  <h2 class="sec-title" style="top:55px"><span>INVESTOR LOGIN</span></h2>
  <p class="sec-sub" style="top:108px">Norvell Hub Investment Partners</p>
  <div class="field" style="left:215px;width:311px">User Name *</div>
  <div class="field" style="left:538px;width:312px">Password *</div>
  <div class="submit">SUBMIT</div>
</section>

<!-- news -->
<span class="timeline"></span>
<h2 class="sec-title" style="top:2993px"><span>LATEST NEWS</span></h2>
<p class="sec-sub" style="top:3047px">Press Release &amp; Portfolio News</p>

<div class="news-thumb" style="left:206px;top:3131px"><div style="background:radial-gradient(ellipse 30px 50px at 30% 60%,#101a30,rgba(16,26,48,0) 100%),radial-gradient(circle at 65% 45%,#bfe0ff 0,rgba(191,224,255,0) 25%),radial-gradient(circle,#6f95bd,#1d2f52)" role="img" aria-label="Businessman with a rising growth chart"></div></div>
<p class="news-date" style="top:3144px">April 30, 2018</p>
<h3 class="news-title" style="top:3180px">NORVELL HUB COMPLETES STRUCTURED DEBT INVESTMENT IN LEAFPOINT</h3>
<p class="news-text" style="top:3240px">Norvell Hub Partners (“Norvell Hub”) announced today that it has completed a structured debt investment in LeafPoint, Inc.</p>

<div class="news-thumb" style="left:206px;top:3395px"><div style="background:radial-gradient(ellipse 35px 45px at 30% 65%,#2a4a66,rgba(42,74,102,0) 100%),radial-gradient(circle at 65% 40%,#d8eef8 0,rgba(216,238,248,0) 30%),radial-gradient(circle,#8fbcd4,#2b5470)" role="img" aria-label="Analyst viewing financial dashboards"></div></div>
<p class="news-date" style="top:3405px">april 4, 2016</p>
<h3 class="news-title" style="top:3441px">CORVEX SEMICONDUCTOR ACQUIRED BY HALVANE FOR $55,000,000</h3>
<p class="news-text" style="top:3501px">Halvane Optics, Inc., a leading supplier of advanced semi - conductor communications components for use in Cloud connectivity, data centers,</p>

<div class="news-thumb" style="left:206px;top:3656px"><div style="background:radial-gradient(ellipse 25px 50px at 45% 50%,#1a1f2c,rgba(26,31,44,0) 100%),radial-gradient(circle,#9fb3cc,#3a4c68 70%,#222d40)" role="img" aria-label="Metallic dollar sign on a blue background"></div></div>
<p class="news-date" style="top:3666px">OCTOBER 19, 2016</p>
<h3 class="news-title" style="top:3702px">NORVELL HUB COMPLETES $22,000,000 STRUCTURED DEBT INVESTMENT IN POLLARIS</h3>
<p class="news-text" style="top:3762px">Norvell Hub Partners (“Norvell Hub”) announced today that it has completed a $22,000,000 structured debt investment in Pollaris AS (“</p>

<footer class="site-footer">
  <div class="brand"><span class="dot"></span>Norvell Hub</div>
  <p class="foot-line" style="top:135px">SAN FRANCISCO</p>
  <p class="foot-line" style="top:160px">2150 Harlow Street #318</p>
  <p class="foot-line" style="top:183px">San Francisco, CA&nbsp; 94107</p>
  <p class="foot-line" style="top:236px;font-size:14px">Home&nbsp; | &nbsp;Strategy&nbsp; | &nbsp;About Us&nbsp; | &nbsp;Team&nbsp; | &nbsp;News&nbsp; | &nbsp;Contact&nbsp; | &nbsp;Investor</p>
  <p class="foot-line" style="top:266px;font-size:14px">©2019 Norvell Hub Partners LLC.&nbsp; All Rights Reserved.</p>
</footer>

</body>
</html>
```